"Fight Back" banner ad design

We have sketched the design and have images to consider including. We are looking for something striking, FIGHT BACK! with a clenched fist image, then a fading images of variance.png and hi-bill.png in the background. Tag line "Fight your water bill with your own data" optionally include "Tally Mode" rivo3196 logo, KPMT Design, LLC based in San Diego CA. Pre-order now, visit https://www.fundbeacon.com/rivometer @rivo3196, info@rivo3196.com

"Fight your water bill with your own data"

```html
<!DOCTYPE html>
<html lang="en">
<head>
<meta charset="utf-8">
<title>Fight Back – Water Bill Banner</title>
<link rel="stylesheet" href="https://fonts.googleapis.com/css2?family=Montserrat:wght@700;800&family=Lexend+Deca:wght@500;600&family=Arimo:wght@700&display=swap">
<style>
  :root {
    --teal: #3a7886;
    --teal-dark: #245d69;
    --teal-light: #8ccbdc;
    --navy: #173b68;
    --ink: #111111;
    --button-top: #7fb0e6;
    --button-bottom: #3a74c2;
    --paper: #ffffff;
    --skin-light: #efc7a3;
    --skin-dark: #c98e63;
  }
  * { margin: 0; padding: 0; box-sizing: border-box; }
  html, body { width: 1200px; height: 663px; overflow: hidden; background: var(--paper); }
  .banner {
    position: relative; width: 1200px; height: 663px; overflow: hidden;
    background: var(--paper);
    font-family: "Lexend Deca", sans-serif;
  }
  .bill-backdrop {
    position: absolute; left: 268px; top: 16px; width: 456px; height: 647px;
    background: linear-gradient(180deg, rgba(200,215,220,0.45), rgba(235,240,242,0.35) 40%, rgba(220,228,232,0.35));
    filter: blur(2px);
  }
  .fist-photo {
    position: absolute; left: 0; top: 0; width: 720px; height: 400px;
    background:
      radial-gradient(ellipse 42% 55% at 55% 62%, var(--skin-dark), transparent 70%),
      radial-gradient(ellipse 60% 70% at 50% 40%, var(--skin-light), transparent 72%);
  }
  .headline {
    position: absolute; left: 492px; top: 22px;
    white-space: nowrap;
    font-family: "Montserrat", sans-serif; font-weight: 800;
    font-size: 100px; line-height: 100px; letter-spacing: -1px;
    color: var(--teal);
    background: var(--paper); padding: 0 6px; border-radius: 6px;
  }
  .tagline {
    position: absolute; left: 730px; top: 136px;
    white-space: nowrap;
    font-weight: 600; font-size: 42px; line-height: 56px;
    color: var(--navy);
  }
  .usage-chart { position: absolute; left: 557px; top: 262px; width: 637px; height: 384px; }
  .chart-text { font-family: "Arimo", sans-serif; font-weight: 700; }
  .startup-note {
    position: absolute; left: 8px; top: 448px;
    white-space: nowrap;
    font-weight: 500; font-size: 26px; line-height: 34px; color: var(--ink);
  }
  .preorder-button {
    position: absolute; left: 12px; top: 532px; width: 346px; height: 44px;
    border-radius: 4px;
    background: linear-gradient(180deg, var(--button-top), var(--button-bottom));
    box-shadow: 0 0 0 4px #e4eef9;
    color: var(--paper); font-family: "Arimo", sans-serif; font-weight: 700;
    font-size: 32px; line-height: 44px; padding-left: 38px;
    white-space: nowrap;
  }
  .preorder-button .chevron { position: absolute; right: 30px; top: 0; font-size: 28px; }
  .social-mark {
    position: absolute; left: 378px; top: 528px;
    display: flex; align-items: center; gap: 6px;
    font-weight: 600; font-size: 20px; color: var(--button-bottom);
  }
  .social-mark .dot { width: 14px; height: 14px; border-radius: 50%; background: var(--button-bottom); }
  .brand-name {
    position: absolute; left: 450px; top: 597px;
    font-weight: 600; font-size: 20px; color: var(--teal);
  }
  .contact {
    position: absolute; left: 8px; top: 584px;
    white-space: nowrap;
    font-weight: 500; font-size: 23px; line-height: 33px; color: var(--ink);
  }
</style>
</head>
<body>
<div class="banner">
  <div class="bill-backdrop" role="img" aria-label="Faded water bill statement in the background"></div>
  <div class="fist-photo" role="img" aria-label="Clenched fist crumpling a printed water bill receipt"></div>

  <h1 class="headline">FIGHT BACK!</h1>
  <p class="tagline">Fight your water bill<br>with your own data.</p>

  <svg class="usage-chart" viewBox="0 0 637 384" aria-label="Water use in HCF, previous year versus current year">
    <rect x="1" y="1" width="635" height="382" fill="#fff" stroke="var(--teal-dark)" stroke-width="2"/>
    <rect x="0" y="0" width="637" height="30" fill="var(--teal-dark)"/>
    <text class="chart-text" x="318" y="22" fill="#fff" font-size="22" text-anchor="middle">WATER USE IN HCF (Hundred Cubic Feet)</text>
    <rect x="165" y="39" width="16" height="16" fill="var(--teal-light)" stroke="#555" stroke-width="1"/>
    <text x="190" y="53" font-family="Arimo, sans-serif" font-size="15" fill="#111">Previous Year</text>
    <rect x="331" y="39" width="16" height="16" fill="var(--teal-dark)"/>
    <text x="356" y="53" font-family="Arimo, sans-serif" font-size="15" fill="#111">Current Year</text>
    <g stroke="#111" stroke-width="1.5">
      <line x1="35" y1="62" x2="625" y2="62"/><line x1="35" y1="82" x2="625" y2="82"/>
      <line x1="35" y1="101" x2="625" y2="101"/><line x1="35" y1="121" x2="625" y2="121"/>
      <line x1="35" y1="141" x2="625" y2="141"/><line x1="35" y1="161" x2="625" y2="161"/>
      <line x1="35" y1="180" x2="625" y2="180"/><line x1="35" y1="200" x2="625" y2="200"/>
      <line x1="35" y1="220" x2="625" y2="220"/><line x1="35" y1="240" x2="625" y2="240"/>
      <line x1="35" y1="259" x2="625" y2="259"/><line x1="35" y1="279" x2="625" y2="279"/>
      <line x1="35" y1="299" x2="625" y2="299"/><line x1="35" y1="319" x2="625" y2="319"/>
      <line x1="35" y1="338" x2="625" y2="338"/><line x1="35" y1="358" x2="625" y2="358"/>
      <line x1="35" y1="378" x2="625" y2="378"/>
    </g>
    <g font-family="Arimo, sans-serif" font-size="14" fill="#111" text-anchor="end">
      <text x="30" y="67">80</text><text x="30" y="87">75</text><text x="30" y="106">70</text>
      <text x="30" y="126">65</text><text x="30" y="146">60</text><text x="30" y="166">55</text>
      <text x="30" y="185">50</text><text x="30" y="205">45</text><text x="30" y="225">40</text>
      <text x="30" y="245">35</text><text x="30" y="264">30</text><text x="30" y="284">25</text>
      <text x="30" y="304">20</text><text x="30" y="324">15</text><text x="30" y="343">10</text>
      <text x="30" y="363">5</text><text x="30" y="383">0</text>
    </g>
    <g fill="var(--teal-light)" stroke="#9bb" stroke-width="1">
      <rect x="86" y="271" width="20" height="107"/>
      <rect x="186" y="244" width="20" height="134"/>
      <rect x="284" y="303" width="20" height="75"/>
      <rect x="384" y="261" width="20" height="117"/>
      <rect x="482" y="279" width="20" height="99"/>
      <rect x="582" y="279" width="20" height="99"/>
    </g>
    <g fill="var(--teal-dark)">
      <rect x="110" y="287" width="20" height="91"/>
      <rect x="210" y="299" width="20" height="79"/>
      <rect x="308" y="299" width="20" height="79"/>
      <rect x="408" y="66" width="20" height="312"/>
      <rect x="506" y="109" width="20" height="269"/>
      <rect x="606" y="90" width="20" height="288"/>
    </g>
  </svg>

  <p class="startup-note">Change "LLC based in San Diego CA<br>to a San Diego startup</p>

  <div class="preorder-button">Pre-order now <span class="chevron">›</span></div>

  <div class="social-mark"><span class="dot"></span>Chirpnet</div>
  <div class="brand-name">rivo3196</div>

  <p class="contact">Visit https://www.fundbeacon.com<br>rivometer@rivo3196, info@rivo3196.com</p>
</div>
</body>
</html>
```